Business Card Design Project : Ridgeline Press

In preparation for market launch, Tamarind's Ridgeline Press require the development of a business card. Ridgeline Press is a Community online publishing web portal. We provide the the city of Whistler located in B.C. (Canada) business directories, News, Classified ads, News, Events and blogs etc.

The main focus of the brand is to help local businesses to corporate with their online advertisement and marketing. Meeting our clients face to face is a must (B2B).

Target Market(s)

The target market is B2B customers. Business Owners to Marketing, advertising Managers

Industry/Entity Type

Business

Requirements
Must have
• - The business card will be two sided.
the BACK side will have our logo which consist of (icon, url,slogan) submited. The logo will be middle and centred.

The FRONT side should have company details:

Company Legal Name: TAMARIND RIDGELINE MEDIA

Owen Farsk
Director of Sales & Marketing

www.tamarindridgeline.biz
owen@tamarindridgeline.biz

Phone: 604 317 8842
#2714 - 582 E. Halvern St.
Vancouver, B.C. V7K2R4 Canada
Nice to have
• - For the "FRONT" side of our business card. You can separate or re-arrange with our logo components (icon, logo,slogan). It does not have to be together.

Also our company legal name is rather long so arrange or organize the name in a way to make it shorter. Your experience and creativity will have to come in play.
Should not have
• should not have other colors beside logo color and black text (2 colors). Also nothing Three dimensional

```html
<!DOCTYPE html>
<html lang="en">
<head>
<meta charset="utf-8">
<title>Ridgeline Press – Business Card</title>
<link rel="stylesheet" href="https://fonts.googleapis.com/css2?family=Mulish:wght@700;800&family=Source+Sans+3:wght@400;600;700&display=swap">
<style>
  :root {
    --brand-blue: #0b7cd0;
    --ink: #111111;
    --paper: #ffffff;
    --backdrop: #e9e6e1;
    --faint: #efefef;
    --text-font: "Source Sans 3", Arial, sans-serif;
    --name-font: "Mulish", Arial, sans-serif;
  }
  * { margin: 0; padding: 0; box-sizing: border-box; }
  html, body { width: 1200px; height: 1000px; overflow: hidden; }
  body { background: var(--backdrop); position: relative; font-family: var(--text-font); }

  .card { position: absolute; overflow: hidden; }

  /* Back side */
  .card-back {
    left: 37px; top: 37px; width: 750px; height: 443px;
    background: var(--brand-blue);
  }
  .card-back .base-band {
    position: absolute; left: 0; bottom: 0; width: 100%; height: 27px;
    background: var(--ink);
  }
  .back-lockup {
    position: absolute; left: 0; right: 0; top: 118px;
    text-align: center;
  }
  .brand-name {
    font-family: var(--text-font); font-weight: 700;
    display: inline-flex; align-items: center; gap: 14px;
  }
  .brand-name .dot { width: 22px; height: 22px; border-radius: 50%; display: inline-block; }
  .card-back .brand-name { color: var(--paper); font-size: 46px; }
  .card-back .brand-name .dot { background: var(--paper); }
  .card-back .url {
    margin-top: 34px; font-size: 30px; font-weight: 700; color: var(--ink); letter-spacing: 0.2px;
  }
  .card-back .slogan { margin-top: 2px; font-size: 25px; color: var(--paper); }

  /* Front side */
  .card-front {
    left: 395px; top: 521px; width: 749px; height: 442px;
    background: var(--paper);
  }
  .card-front .base-band {
    position: absolute; left: 0; bottom: 0; width: 100%; height: 26px;
    background: var(--brand-blue);
  }
  .faint-mark {
    position: absolute; left: 150px; top: 190px;
    font-family: var(--text-font); font-weight: 700; font-size: 78px;
    color: var(--faint); white-space: nowrap;
  }
  .front-lockup {
    position: absolute; right: 40px; top: 48px; width: 300px; text-align: center;
  }
  .card-front .brand-name { color: var(--brand-blue); font-size: 30px; }
  .card-front .brand-name .dot { background: var(--brand-blue); width: 16px; height: 16px; }
  .card-front .url { margin-top: 22px; font-size: 22px; font-weight: 700; color: var(--ink); }
  .card-front .slogan { font-size: 16.5px; color: var(--brand-blue); font-weight: 600; }

  .person { position: absolute; left: 40px; top: 86px; }
  .person .name {
    font-family: var(--name-font); font-weight: 800; font-size: 44px;
    color: var(--brand-blue); line-height: 1;
  }
  .person .role { margin-top: 14px; font-size: 18px; color: var(--ink); }

  .contacts { position: absolute; left: 40px; top: 192px; font-size: 18px; color: var(--ink); line-height: 27px; }
  .contacts .label { color: var(--brand-blue); }
  .contacts .group + .group { margin-top: 10px; }

  .company { position: absolute; left: 40px; top: 324px; font-size: 18px; line-height: 23px; color: var(--ink); }
  .company .legal-name { font-weight: 700; color: var(--brand-blue); letter-spacing: 0.3px; }
</style>
</head>
<body>

  <section class="card card-back" aria-label="Business card back">
    <div class="back-lockup">
      <div class="brand-name"><span class="dot"></span>Ridgeline Press</div>
      <div class="url">www.tamarindridgeline.biz</div>
      <div class="slogan">Your information gateway</div>
    </div>
    <div class="base-band"></div>
  </section>

  <section class="card card-front" aria-label="Business card front">
    <div class="faint-mark" aria-hidden="true">Ridgeline Press</div>

    <div class="front-lockup">
      <div class="brand-name"><span class="dot"></span>Ridgeline Press</div>
      <div class="url">www.tamarindridgeline.biz</div>
      <div class="slogan">Your information gateway</div>
    </div>

    <div class="person">
      <div class="name">Owen Farsk</div>
      <div class="role">Director of Sales &amp; Marketing</div>
    </div>

    <div class="contacts">
      <div class="group">
        <div><span class="label">phone:</span> 604 317 8842</div>
        <div><span class="label">mob:</span>+00(0)0 00000000</div>
      </div>
      <div class="group">
        <div><span class="label">e-mail:</span> owen@tamarindridgeline.biz</div>
        <div><span class="label">web:</span> www.tamarindridgeline.biz</div>
      </div>
    </div>

    <div class="company">
      <div class="legal-name">TAMARIND RIDGELINE MEDIA</div>
      <div>#2714 - 582 E. Halvern St.</div>
      <div>Vancouver, B.C. V7K2R4 Canada</div>
    </div>

    <div class="base-band"></div>
  </section>

</body>
</html>
```